Web Design

We need a website for a company based in Doha Qatar called
Lumara Maid Service.

It is the number one maid cleaning service company, and we have branches all over qatar.

Luxury Cleaning Service Provider.

The color scheme is gold, yellow and black like the logo.

Before they get to the website, there is an intro video.

The website should depict luxury.

Target Market(s)

People who need maids at their houses.

Industry/Entity Type

Cleaning Service

Requirements
Must have
• Luxury, Sleek, Modern

The opening sequence is a video which I already have. Its too big to upload here so I am going to put it on youtube.

After the opening sequence, the home page should have a widescreen photo background and it should change every five seconds, the first background photo should be of qatar westbay skyline. Then the second background should be of maid photos in cleaning positions. Then the third background should be of cleaner photos etc.

We will send you all the tabs and all the content later.

```html
<!DOCTYPE html>
<html lang="en">
<head>
<meta charset="utf-8">
<title>Lumara Maid Service</title>
<link href="https://fonts.googleapis.com/css2?family=Nunito:wght@400;600;700&display=swap" rel="stylesheet">
<style>
  :root {
    --page-yellow: #fdf4a3;
    --gold: #d99f31;
    --gold-bright: #fbbd3c;
    --gold-text: #f8b62a;
    --button: #fcc144;
    --ink: #1a1a1a;
    --muted: #5a5a5a;
    --white: #ffffff;
    --red: #d0140e;
  }
  * { margin: 0; padding: 0; box-sizing: border-box; }
  html, body { width: 1200px; height: 1116px; overflow: hidden; }
  body {
    position: relative;
    background: var(--page-yellow);
    font-family: "Nunito", sans-serif;
    color: var(--ink);
  }
  .abs { position: absolute; }

  /* Hero */
  .hero {
    left: 100px; top: 0; width: 1000px; height: 501px;
    background:
      linear-gradient(90deg, rgba(255,255,255,0) 0%, rgba(255,255,255,0) 62%, rgba(70,90,115,.22) 78%, rgba(60,80,105,.30) 100%),
      linear-gradient(180deg,
        #fbfbfd 0%, #eef0f6 18%, #dde1e8 34%, #cfd3d8 52%,
        #b9bfc1 60%, #a2adb1 64%, #94a2a7 72%, #8d9a9c 78%,
        #9a958a 84%, #857f73 91%, #6e695f 100%);
  }
  .brand { left: 140px; top: 62px; display: flex; align-items: center; gap: 10px; }
  .brand-dot { width: 22px; height: 22px; border-radius: 50%; background: var(--gold-bright); }
  .brand-name { font-size: 19px; font-weight: 700; color: #8a5a17; letter-spacing: .3px; }
  .call-now { left: 845px; top: 20px; font-size: 14px; color: #7a7a7a; }
  .call-now strong { font-size: 22px; font-weight: 600; color: #7a7a7a; }
  .main-nav {
    left: 372px; top: 88px; width: 708px; height: 50px;
    border-radius: 25px; background: rgba(255,255,255,.78);
    border: 1px solid rgba(255,255,255,.95);
    display: flex; align-items: center; padding-left: 44px; gap: 19px;
  }
  .main-nav a { font-size: 14.5px; color: #4a2d0c; text-decoration: none; }
  .slider-arrow {
    top: 457px; width: 30px; height: 30px; background: rgba(255,255,255,.35);
    border: 1px solid rgba(255,255,255,.6);
  }

  /* About */
  .about {
    left: 100px; top: 505px; width: 262px; height: 316px;
    background: var(--gold); border-radius: 26px 0 0 26px; color: var(--white);
  }
  .about h2 { position: absolute; left: 60px; top: 16px; font-size: 25px; font-weight: 600; }
  .about .rule { position: absolute; left: 0; right: 0; top: 60px; height: 1px; background: rgba(255,255,255,.35); }
  .about p { position: absolute; left: 22px; width: 222px; font-size: 12.6px; line-height: 15.5px; }
  .btn {
    position: absolute; width: 97px; height: 32px; border-radius: 8px;
    background: var(--button); color: #3b2606; font-size: 13.5px;
    display: flex; align-items: center; justify-content: center;
  }

  /* Services */
  .services {
    left: 358px; top: 505px; width: 461px; height: 316px;
    background: var(--white); border-radius: 0 22px 22px 0;
    border: 1px solid #f0e6b8;
  }
  .services h2 { position: absolute; left: 13px; top: 14px; font-size: 25px; font-weight: 600; }
  .service-photo {
    position: absolute; left: 12px; top: 49px; width: 218px; height: 93px;
    border: 3px solid #e6e6e6; border-radius: 8px;
    background: linear-gradient(90deg, #ffffff 0%, #f4eee6 45%, #e8c59a 60%, #f1f1f1 100%);
  }
  .services h3 { position: absolute; left: 21px; top: 152px; font-size: 19px; font-weight: 400; }
  .services p { position: absolute; left: 22px; top: 186px; width: 232px; font-size: 12.6px; line-height: 15.5px; }
  .service-list { position: absolute; left: 275px; top: 30px; list-style: none; }
  .service-list li {
    position: relative; height: 36px; width: 150px; padding-left: 29px;
    display: flex; align-items: center; font-size: 14px;
  }
  .service-list li::before {
    content: ""; position: absolute; left: 0; top: 13px;
    border-left: 5px solid var(--ink); border-top: 4px solid transparent; border-bottom: 4px solid transparent;
  }
  .service-list li.active::after {
    content: ""; position: absolute; left: 15px; top: 0; width: 150px; height: 36px;
    background: #000; border-radius: 6px; z-index: 0;
  }
  .service-list li span { position: relative; z-index: 1; }
  .service-list li.active span { color: var(--gold-bright); }

  /* Call circle */
  .call-badge {
    left: 859px; top: 537px; width: 168px; height: 168px; border-radius: 50%;
    background: #000; border: 3px solid var(--gold-bright);
    text-align: center; color: var(--white);
  }
  .call-badge .label { margin-top: 32px; font-size: 18px; color: var(--gold-bright); }
  .call-badge .number { font-size: 23px; font-weight: 600; margin-top: 2px; letter-spacing: -.3px; }
  .call-badge .sub { font-size: 12px; color: var(--gold-bright); margin-top: 2px; }
  .call-badge .alt { font-size: 16px; font-weight: 700; color: var(--gold-bright); margin-top: 4px; }
  .side-text { left: 839px; top: 726px; width: 240px; font-size: 12.6px; line-height: 15.5px; }

  /* Testimonials & clients */
  .section-title { font-size: 17px; font-weight: 700; color: var(--gold-text); letter-spacing: .2px; }
  .quote-mark { font-size: 34px; color: #bdbdbd; font-family: Georgia, serif; font-style: italic; }
  .testimonial { left: 149px; top: 890px; width: 480px; font-size: 12.6px; line-height: 15.5px; }
  .author { left: 146px; top: 939px; font-size: 13px; }
  .author span { color: var(--red); }
  .client-row { left: 660px; top: 900px; display: flex; gap: 14px; align-items: center; }
  .client { display: flex; align-items: center; gap: 5px; font-size: 13px; font-weight: 700; color: #7a1a10; }
  .client i { width: 12px; height: 12px; border-radius: 50%; background: var(--red); display: block; }

  /* Footer */
  .divider { left: 115px; top: 992px; width: 960px; height: 1px; background: #d9d09a; }
  .footer-nav { left: 136px; top: 1041px; display: flex; gap: 18px; }
  .footer-nav a { font-size: 13px; color: var(--muted); text-decoration: none; }
  .social { top: 1035px; width: 30px; height: 30px; border-radius: 3px; }
  .copyright { left: 833px; top: 1084px; font-size: 13px; color: var(--muted); }
</style>
</head>
<body>

<div class="abs hero" role="img" aria-label="Wide photo of the West Bay skyline and bay seen from above"></div>

<div class="abs brand">
  <span class="brand-dot"></span>
  <span class="brand-name">Lumara Maid Service</span>
</div>

<div class="abs call-now">CALL NOW : <strong>1800 472 910</strong></div>

<nav class="abs main-nav">
  <a href="#">Home</a><a href="#">About Us</a><a href="#">Cleaning Service</a><a href="#">Products</a>
  <a href="#">References</a><a href="#">Clients</a><a href="#">Career</a><a href="#">Contact</a>
</nav>

<div class="abs slider-arrow" style="left:1012px">
  <svg width="30" height="30" viewBox="0 0 30 30"><path d="M19 5 L9 15 L19 25" fill="none" stroke="#fff" stroke-width="1.5"/></svg>
</div>
<div class="abs slider-arrow" style="left:1051px">
  <svg width="30" height="30" viewBox="0 0 30 30"><path d="M11 5 L21 15 L11 25" fill="none" stroke="#fff" stroke-width="1.5"/></svg>
</div>

<section class="abs about">
  <h2>ABOUT US</h2>
  <div class="rule"></div>
  <p style="top:70px">Neque porro quisquam est, qui dolorem ipsum quia dolor sit amet, consectetur, adipisci velit, sed quia non numquam eius modi tempora incidunt ut labore et dolore magnam aliquam</p>
  <p style="top:179px">But who has any right to find fault with a man who chooses to enjoy a pleasure that has no annoying consequences</p>
  <span class="btn" style="left:142px;top:260px">Read more</span>
</section>

<section class="abs services">
  <h2>OUR SRVICES</h2>
  <div class="service-photo" role="img" aria-label="Photo of a cleaner holding a basket of cleaning supplies"></div>
  <h3>Industrial Cleaning</h3>
  <p>Neque porro quisquam est, qui dolorem ipsum quia dolor sit amet, consectetur, adipisci velit, sed quia non numquam eius modi tempora .</p>
  <span class="btn" style="left:21px;top:260px">Read more</span>
  <ul class="service-list">
    <li><span>House Cleaning</span></li>
    <li><span>School Cleaning</span></li>
    <li><span>Hospital Cleaning</span></li>
    <li class="active"><span>Industrial Cleaning</span></li>
    <li><span>Roof Cleaning</span></li>
    <li><span>Specialist Cleaning</span></li>
  </ul>
</section>

<div class="abs call-badge">
  <div class="label">CALL US</div>
  <div class="number">44 310 27 58</div>
  <div class="sub">for mobile phones</div>
  <div class="alt">1800 639 104</div>
</div>
<p class="abs side-text">Neque porro quisquam est, qui dolorem ipsum quia dolor sit amet, consectetur, adipisci velit, sed quia non numquam eius modi tempora .</p>

<h2 class="abs section-title" style="left:125px;top:844px">CLIENT TESTIMONIALS</h2>
<span class="abs quote-mark" style="left:124px;top:872px">“</span>
<p class="abs testimonial">Neque porro quisquam est, qui dolorem ipsum quia dolor sit amet, consectetur, adipisci velit, sed quia non numquam eius modi tempora .</p>
<span class="abs quote-mark" style="left:498px;top:900px">”</span>
<p class="abs author">Omar Haddad, <span>Harbor Grill</span></p>

<h2 class="abs section-title" style="left:660px;top:844px">WE WORK FOR</h2>
<div class="abs client-row">
  <span class="client"><i></i>Harbor Grill</span>
  <span class="client"><i></i>Corniche Foods</span>
  <span class="client"><i></i>Dunemotor</span>
  <span class="client"><i></i>Fizzo</span>
</div>

<div class="abs divider"></div>

<nav class="abs footer-nav">
  <a href="#">Home</a><a href="#">About Us</a><a href="#">Cleaning Service</a><a href="#">Products</a>
  <a href="#">References</a><a href="#">Clients</a><a href="#">Career</a><a href="#">Contact</a>
</nav>

<span class="abs social" style="left:854px;background:#4d6fb3"></span>
<span class="abs social" style="left:904px;background:#5bb8d8"></span>
<span class="abs social" style="left:958px;background:#3b78b8"></span>
<span class="abs social" style="left:1008px;background:#f08a1c"></span>

<p class="abs copyright">© 2014.www.lumaramaid.com</p>

</body>
</html>
```